Business Card Design Project

Looking for a logo and business card for a Real State Business i will be opening. The name is not choosen yet , but will probably be RWT IMOVEIS.
I was thinking black and silver colors, but am open to nice ideas.
I did add a business card that i liked a lot, am looking for something like that, with logo in black or silver in a black card. The logo i was thinking in the letters RWT as i uploaded or something or little and cute buildings or a house...just ideas, can be any nice logo.
Updates

You guys can add other colors if you want, I like colors very "BRIGHT" and "open", like red, pink, strong colors. almost glow in the dark colors. lol

Designers,

I've increased more 88 dollars in the budget for 1st place cause I will want envelope designs... small and big sizes.

So 1st place is now U$248,00. 

No need to send the envelope designs right now... only the business cards designs.

Thank you.

Industry/Entity Type

Business

Requirements
Must have
• Marcela Tavares Rocha

www.RWTimoveis-exemplo.com.br

+554187316042

marcela@rwtimoveis-exemplo.com.br

```html
<!DOCTYPE html>
<html lang="pt-BR">
<head>
<meta charset="UTF-8">
<title>RWT Imóveis – Cartão de Visita</title>
<link href="https://fonts.googleapis.com/css2?family=Arimo:wght@400;700&display=swap" rel="stylesheet">
<style>
  :root {
    --page-bg: #ffffff;
    --card-bg: #0b0a07;
    --accent-yellow: #ffe600;
    --text-white: #ffffff;
  }
  * { margin: 0; padding: 0; box-sizing: border-box; }
  html, body {
    width: 1000px;
    height: 1200px;
    overflow: hidden;
    background: var(--page-bg);
    font-family: "Arimo", Arial, sans-serif;
  }
  .card {
    position: absolute;
    left: 92px;
    width: 816px;
    height: 472px;
    background: var(--card-bg);
    overflow: hidden;
  }
  .card--front { top: 109px; }
  .card--back  { top: 619px; }

  .brand {
    position: absolute;
    display: flex;
    align-items: flex-start;
    white-space: nowrap;
  }
  .brand__name {
    color: var(--accent-yellow);
    font-weight: 400;
    line-height: 1;
  }
  .brand__mark {
    background: var(--text-white);
    flex: none;
  }
  .card--front .brand {
    left: 112px;
    top: 223px;
    gap: 8px;
  }
  .card--front .brand__name {
    font-size: 70px;
    letter-spacing: -2px;
  }
  .card--front .brand__mark {
    width: 14px;
    height: 14px;
    margin-top: 8px;
  }
  .card--back .brand {
    left: 50%;
    top: 206px;
    transform: translateX(-50%);
    gap: 14px;
  }
  .card--back .brand__name {
    font-size: 133px;
    letter-spacing: -4px;
  }
  .card--back .brand__mark {
    width: 26px;
    height: 26px;
    margin-top: 16px;
  }

  .divider {
    position: absolute;
    left: 315px;
    top: 78px;
    width: 3px;
    height: 315px;
    background: var(--accent-yellow);
  }

  .contact {
    position: absolute;
    left: 393px;
    top: 143px;
    font-weight: 700;
    white-space: nowrap;
  }
  .contact__name {
    color: var(--accent-yellow);
    font-size: 27px;
    line-height: 1;
    margin-bottom: 21px;
  }
  .contact__line {
    color: var(--text-white);
    font-size: 19px;
    line-height: 30px;
  }
  .contact__web {
    margin-top: 56px;
  }
</style>
</head>
<body>
  <section class="card card--front" aria-label="Frente do cartão">
    <div class="brand">
      <span class="brand__name">RWT</span>
      <span class="brand__mark"></span>
    </div>
    <div class="divider"></div>
    <div class="contact">
      <p class="contact__name">Marcela Tavares Rocha</p>
      <p class="contact__line">marcela@rwtimoveis-exemplo.com.br</p>
      <p class="contact__line">0055 418 731 6042</p>
      <p class="contact__line contact__web">www.RWTimoveis-exemplo.com.br</p>
    </div>
  </section>

  <section class="card card--back" aria-label="Verso do cartão">
    <div class="brand">
      <span class="brand__name">RWT</span>
      <span class="brand__mark"></span>
    </div>
  </section>
</body>
</html>
```